Verodex business card

Business card for sustainable investment company called "Verodex". Verodex is an exchange platform selling carbon credits between buyers and sellers. Carbon Credits are an environmental commodity for reducing global carbon emissions.

the card should obviously have our logo and the theme should be sustainability/environment mixed with a trading platform.

Contact Information for Business Card

Logo, Name, Title, Phone, Email

Colors
0054AA
0677BA
7BADD7
CADEEF
E8F1F8
0094D4
00A9DD
6FCCEA
C7EBF8
E9F6FB
00AB8E
00BBA5
67D7C9
C6EFE9
E9F9F6
59FF00
82FF00
B8FF75
E3FFCB
F4FFEA

```html
<!DOCTYPE html>
<html lang="en">
<head>
<meta charset="utf-8">
<title>Verodex Business Card</title>
<link href="https://fonts.googleapis.com/css2?family=Montserrat:wght@400;500;600;700&display=swap" rel="stylesheet">
<style>
  :root {
    --page-bg: #3a3a3c;
    --navy: #162a52;
    --white: #ffffff;
    --ink-light: #e9eef6;
    --accent-start: #5bc4d9;
    --accent-end: #4a74c2;
    --icon-blue: #4aa8d8;
    --emboss: #2b5580;
  }
  * { margin: 0; padding: 0; box-sizing: border-box; }
  html, body {
    width: 1200px; height: 1059px; overflow: hidden;
    background: var(--page-bg);
    font-family: "Montserrat", sans-serif;
  }
  .card {
    position: absolute;
    width: 690px; height: 392px;
    border-radius: 20px;
    overflow: hidden;
    box-shadow: 0 14px 28px rgba(0,0,0,.45);
  }
  .card--front { left: 255px; top: 100px; background: var(--navy); }
  .card--back { left: 255px; top: 537px; background: var(--navy); }

  .front-top {
    position: absolute; left: 0; top: 0; width: 100%; height: 217px;
    background: var(--white);
  }
  .accent-rule {
    position: absolute; left: 0; top: 208px; width: 100%; height: 4px;
    background: linear-gradient(90deg, var(--accent-start), var(--accent-end));
  }
  .name-marker {
    position: absolute; left: 0; top: 85px; width: 14px; height: 41px;
    background: var(--navy);
  }
  .person { position: absolute; left: 30px; top: 82px; color: var(--navy); }
  .person__name { font-size: 26px; font-weight: 700; letter-spacing: .2px; line-height: 1; }
  .person__title { font-size: 17px; font-weight: 400; letter-spacing: .6px; margin-top: 4px; }

  .brand {
    position: absolute; right: 30px; top: 88px;
    display: flex; align-items: center; gap: 14px;
  }
  .brand__square { width: 34px; height: 34px; background: var(--icon-blue); }
  .brand__name { font-size: 40px; font-weight: 700; color: var(--navy); letter-spacing: .5px; line-height: 1; }

  .contact {
    position: absolute; left: 29px; top: 275px; list-style: none;
    color: var(--ink-light); font-size: 16px; letter-spacing: .4px;
  }
  .contact li { display: flex; align-items: center; gap: 8px; height: 26px; }
  .contact svg { width: 13px; height: 13px; fill: var(--icon-blue); flex: none; }

  .address {
    position: absolute; right: 30px; top: 308px; text-align: right;
    color: var(--ink-light); font-size: 16px; line-height: 22px; letter-spacing: .4px;
  }

  .back-brand {
    position: absolute; left: 0; right: 0; top: 0; bottom: 0;
    display: flex; align-items: center; justify-content: center; gap: 22px;
  }
  .back-brand__square { width: 70px; height: 70px; background: var(--emboss); }
  .back-brand__name { font-size: 64px; font-weight: 700; color: var(--emboss); letter-spacing: 1px; line-height: 1; }
</style>
</head>
<body>
  <section class="card card--front">
    <div class="front-top">
      <div class="name-marker"></div>
      <div class="person">
        <div class="person__name">DANA WHITLOW</div>
        <div class="person__title">MANAGER</div>
      </div>
      <div class="brand">
        <div class="brand__square"></div>
        <div class="brand__name">VERODEX</div>
      </div>
    </div>
    <div class="accent-rule"></div>

    <ul class="contact">
      <li>
        <svg viewBox="0 0 24 24" aria-hidden="true"><path d="M6.6 10.8a15 15 0 0 0 6.6 6.6l2.2-2.2a1 1 0 0 1 1-.25 11.4 11.4 0 0 0 3.6.57 1 1 0 0 1 1 1V20a1 1 0 0 1-1 1A17 17 0 0 1 3 4a1 1 0 0 1 1-1h3.5a1 1 0 0 1 1 1c0 1.25.2 2.45.57 3.57a1 1 0 0 1-.25 1z"/></svg>
        555-018-4620
      </li>
      <li>
        <svg viewBox="0 0 24 24" aria-hidden="true"><path d="M2 5h20v2l-10 6L2 7z M2 9l10 6 10-6v10H2z"/></svg>
        hello@verodex.com
      </li>
      <li>
        <svg viewBox="0 0 24 24" aria-hidden="true"><path d="M12 2a10 10 0 1 0 0 20 10 10 0 0 0 0-20zm0 2c.9 0 2.2 1.9 2.7 5H9.3C9.8 5.9 11.1 4 12 4zM4.3 11h3a15 15 0 0 0 0 2h-3a8 8 0 0 1 0-2zm4.9 0h5.6a13 13 0 0 1 0 2H9.2a13 13 0 0 1 0-2zm7.5 0h3a8 8 0 0 1 0 2h-3a15 15 0 0 0 0-2zM9.3 15h5.4c-.5 3.1-1.8 5-2.7 5s-2.2-1.9-2.7-5z"/></svg>
        www.verodex.com
      </li>
    </ul>

    <address class="address" style="font-style:normal">
      2275 Alder Creek Rd. Suite 410<br>
      Harbor Point, OR 97431
    </address>
  </section>

  <section class="card card--back">
    <div class="back-brand">
      <div class="back-brand__square"></div>
      <div class="back-brand__name">VERODEX</div>
    </div>
  </section>
</body>
</html>
```